Group training gym/bootcamp needs a web design

We need a website for our gym that is based in Sydney. We have indoor functional training classes and outdoor bootcamp classes. We would like the web site to have a video (to be created) and photo gallery. I would like the site made on word press and i would like to be able to make minor changes such as changing images and text without having to use a designer.

The website should have the following pages: home page; the gym; the bootcamp; photo gallery; about us; contact.

I have uploaded our logo and i would like to keep to these colour (blue,yellow,silver) and black is also allowed

Target Market(s)

18-50 male and female

Industry/Entity Type

Gym

Coding

Coded - Design and coding required

Number of Pages Required

5+ page

Font styles to use
Sans Serif

Colors
0692cd
fbed22
1b1b1b
e8e8e8

Requirements
Must have
• The website should have the following pages: home page; the gym; the bootcamp; photo gallery; about us; contact.
• I have uploaded our logo and i would like to keep to these colour (blue,yellow,silver) and black is also allowed
• Video upload and photo upload

```html
<!DOCTYPE html>
<html lang="en">
<head>
<meta charset="utf-8">
<title>Coreline Fitness Hub</title>
<link href="https://fonts.googleapis.com/css2?family=Oswald:wght@500;700&family=Lato:wght@400;700&display=swap" rel="stylesheet">
<style>
:root{
  --blue:#1f6fb9;
  --blue-light:#3f8fd2;
  --blue-deep:#0f4f8e;
  --yellow:#f2c014;
  --dark:#1b1b1b;
  --silver:#e8e8e8;
  --grey:#9a9a9a;
  --white:#ffffff;
}
*{margin:0;padding:0;box-sizing:border-box}
html,body{width:1200px;height:3689px;overflow:hidden}
body{position:relative;background:var(--white);font-family:"Lato",Arial,sans-serif;color:var(--dark)}
.abs{position:absolute}
.heading{font-family:"Oswald",Arial,sans-serif;font-weight:700;text-transform:uppercase;letter-spacing:1px}
.btn{position:absolute;display:flex;align-items:center;justify-content:center;font-family:"Lato",Arial,sans-serif;font-weight:700;text-transform:uppercase;font-size:19px;letter-spacing:.5px;outline:2px dashed rgba(255,255,255,.55);outline-offset:-6px}
.btn-yellow{background:var(--yellow);color:var(--dark);outline-color:rgba(0,0,0,.25)}
.btn-blue{background:var(--blue-light);color:var(--white)}
.photo{position:absolute}

/* hero */
.hero{position:absolute;left:0;top:0;width:1200px;height:664px;clip-path:polygon(0 0,100% 0,100% 90.6%,50% 100%,0 90.6%);background:radial-gradient(ellipse at 50% 40%,#6a4a38 0%,#2a1f1a 40%,#0c0c0c 80%)}
.brand{position:absolute;left:84px;top:22px;display:flex;align-items:center;gap:10px}
.brand-mark{width:44px;height:44px;border-radius:50%;background:var(--blue)}
.brand-name{font-family:"Oswald",Arial,sans-serif;font-weight:700;font-size:20px;color:var(--yellow);text-transform:uppercase;line-height:1}
.nav{position:absolute;left:342px;top:31px;display:flex;gap:26px;font-size:15px;text-transform:uppercase;color:var(--white);white-space:nowrap}
.nav .active{color:var(--blue-light)}
.hero-title{position:absolute;left:0;width:1200px;top:250px;text-align:center;font-size:170px;line-height:1;color:var(--blue-light);letter-spacing:4px}
.hero-tag{position:absolute;left:0;width:1200px;top:434px;text-align:center;color:var(--white);font-size:19px;letter-spacing:2px;font-weight:700;text-transform:uppercase}
.chev{position:absolute;width:30px;height:22px}

/* programs */
.programs{position:absolute;left:0;top:602px;width:1200px;height:824px}
.panel-who{position:absolute;left:0;top:0;width:620px;height:372px;background:var(--blue);clip-path:polygon(0 0,100% 14%,97% 100%,0 100%)}
.panel-outdoor{position:absolute;left:0;top:372px;width:600px;height:418px;background:linear-gradient(160deg,#4d4a3a,#2e3b2c 60%,#1f2a20)}
.panel-outdoor::after{content:"";position:absolute;inset:0;background:rgba(10,14,25,.55)}
.panel-indoor{position:absolute;left:600px;top:0;width:600px;height:824px;background:linear-gradient(140deg,#e9edf1,#c9d1d8 45%,#8f9aa4);clip-path:polygon(0 12%,100% 0,100% 100%,0 100%)}
.prog-title{position:absolute;font-size:36px;line-height:1.2;z-index:2}
.prog-text{position:absolute;font-size:14px;line-height:1.55;z-index:2}

/* trainers */
.section-title{position:absolute;left:0;width:1200px;text-align:center;font-size:38px;line-height:1.2;color:var(--blue)}
.trainer{position:absolute;top:1537px;width:298px;height:406px}
.trainer .shape{position:absolute;left:30px;top:78px;width:238px;height:200px}
.trainer .photo{left:60px;top:10px;width:178px;height:268px;border-radius:90px 90px 0 0}
.trainer .card{position:absolute;left:0;top:280px;width:298px;height:126px;border:1px solid #d6d6d6;border-top:none;background:var(--white)}
.trainer .notch{position:absolute;left:0;top:250px;width:298px;height:32px}
.trainer .name{position:absolute;left:0;top:290px;width:298px;text-align:center;font-size:20px}
.trainer .role{position:absolute;left:0;top:324px;width:298px;text-align:center;font-size:14px;color:var(--grey);text-transform:uppercase}
.trainer .socials{position:absolute;left:0;top:352px;width:298px;height:54px;border-top:1px solid #d6d6d6;display:flex;justify-content:center;align-items:center;gap:18px}
.dot{width:36px;height:36px;border-radius:50%;border:1px solid #bdbdbd}

/* gallery */
.gallery{position:absolute;left:0;top:1975px;width:1200px;height:496px;background:radial-gradient(ellipse at 50% 65%,#4a4a4a,#1b1b1b 60%,#0d0d0d);clip-path:polygon(0 0,30% 0,50% 150px,70% 0,100% 0,100% 100%,0 100%)}
.thumbs{position:absolute;left:14px;top:2479px;width:1172px;height:152px;display:flex;gap:6px}
.thumb{flex:1;height:152px}

/* map & contact */
.map{position:absolute;left:0;top:2643px;width:450px;height:591px;background:linear-gradient(160deg,#eeeeee,#e2e2e2)}
.field{position:absolute;border:1px solid #d6d6d6;font-size:13px;color:#aaa;padding:10px 12px}

/* footer */
.footer{position:absolute;left:0;top:3241px;width:1200px;height:393px;background:linear-gradient(90deg,var(--blue-deep),var(--blue) 50%,var(--blue-deep));clip-path:polygon(0 0,50% 115px,100% 0,100% 100%,0 100%)}
.foot-brand{position:absolute;left:204px;top:3400px;width:320px;display:flex;flex-direction:column;align-items:center;gap:10px}
.foot-text{font-size:15px;color:var(--white)}
.foot-social{position:absolute;left:240px;top:3538px;display:flex;gap:10px}
.foot-social .dot{width:42px;height:42px;border:2px solid var(--white)}
.foot-social .dot.on{background:var(--white)}
.foot-info{position:absolute;left:615px;color:var(--white);font-size:15px;line-height:1.5;display:flex;gap:18px;align-items:flex-start}
.copyright{position:absolute;left:0;top:3634px;width:1200px;height:55px;background:#0a0a0a;color:var(--white);font-size:14px;text-align:center;line-height:55px}
.copyright b{color:var(--yellow);font-family:"Oswald",Arial,sans-serif;text-transform:uppercase;letter-spacing:1px}
</style>
</head>
<body>

<!-- Hero -->
<section class="hero" role="img" aria-label="Athlete lifting a barbell overhead on a dark background"></section>
<div class="brand"><span class="brand-mark"></span><span class="brand-name">Coreline<br>Fitness Hub</span></div>
<nav class="nav"><span class="active">Home</span><span>The Gym</span><span>The Bootcamp</span><span>Gallery</span><span>About Us</span><span>Contact</span></nav>
<div class="btn btn-yellow" style="left:944px;top:20px;width:176px;height:48px;font-weight:400">Membership</div>
<h1 class="heading hero-title">Fitness</h1>
<p class="hero-tag">Training hour with Coreline Fitness Hub</p>
<div class="btn btn-yellow" style="left:510px;top:488px;width:180px;height:48px">Find out more</div>
<svg class="chev" style="left:585px;top:646px" viewBox="0 0 30 22"><path d="M4 3l11 7 11-7M4 12l11 7 11-7" fill="none" stroke="#fff" stroke-width="3"/></svg>

<!-- Programs -->
<section class="programs">
  <div class="panel-indoor" role="img" aria-label="Indoor cycling class with trainer and member"></div>
  <div class="panel-outdoor" role="img" aria-label="Outdoor bootcamp group training on grass"></div>
  <div class="panel-who"></div>

  <h2 class="heading prog-title" style="left:80px;top:90px;color:#fff">Who we are</h2>
  <p class="prog-text" style="left:80px;top:152px;width:440px;color:#fff">Lorem Ipsum is simply dummy text of the printing and typesetting industry. Lorem Ipsum has been the industry's standard dummy text ever since the 1500s, when an unknown printer took a galley of type and scrambled it to make a type specimen book.</p>
  <div class="btn btn-blue" style="left:80px;top:258px;width:174px;height:48px;z-index:2">Just do it!</div>

  <h2 class="heading prog-title" style="left:80px;top:470px;color:#fff">Outdoor functional<br>training classes</h2>
  <p class="prog-text" style="left:80px;top:604px;width:440px;color:#fff">Lorem Ipsum is simply dummy text of the printing and typesetting industry. Lorem Ipsum has been the industry's standard dummy text.</p>
  <div class="btn btn-blue" style="left:80px;top:650px;width:174px;height:48px;z-index:2">Read more</div>

  <h2 class="heading prog-title" style="left:700px;top:252px;width:420px;text-align:right;color:var(--blue)">Indoor functional<br>training classes</h2>
  <p class="prog-text" style="left:690px;top:368px;width:430px;text-align:right;color:var(--dark)">Lorem Ipsum is simply dummy text of the printing and typesetting industry. Lorem Ipsum has been the industry's standard dummy text ever since the 1500s, when an unknown printer took a galley of type and scrambled it to make a type specimen book.</p>
  <div class="btn btn-blue" style="left:946px;top:474px;width:174px;height:48px;z-index:2">Read more</div>
</section>

<!-- Trainers -->
<h2 class="heading section-title" style="top:1478px">Trainers</h2>

<article class="trainer" style="left:79px">
  <svg class="shape" viewBox="0 0 238 200" preserveAspectRatio="none"><polygon points="0,40 238,0 238,200 0,200" fill="var(--blue-light)"/></svg>
  <div class="photo" role="img" aria-label="Portrait of a bodybuilder trainer" style="background:linear-gradient(180deg,#8a5a3a,#4a2e1e)"></div>
  <svg class="notch" viewBox="0 0 298 32" preserveAspectRatio="none"><polygon points="0,30 149,2 298,30 298,32 0,32" fill="#fff" stroke="#d6d6d6"/></svg>
  <div class="card"></div>
  <div class="heading name">- Dana Rowe</div>
  <div class="role">Body builder</div>
  <div class="socials"><span class="dot"></span><span class="dot"></span><span class="dot"></span><span class="dot"></span></div>
</article>

<article class="trainer" style="left:450px">
  <svg class="shape" viewBox="0 0 238 200" preserveAspectRatio="none"><polygon points="0,0 238,40 238,200 0,200" fill="var(--yellow)"/></svg>
  <div class="photo" role="img" aria-label="Portrait of a fitness model trainer" style="background:linear-gradient(180deg,#e0c89a,#b0a49a)"></div>
  <svg class="notch" viewBox="0 0 298 32" preserveAspectRatio="none"><polygon points="0,30 149,2 298,30 298,32 0,32" fill="#fff" stroke="#d6d6d6"/></svg>
  <div class="card"></div>
  <div class="heading name" style="color:var(--blue)">- Dana Rowe</div>
  <div class="role">Fitness model</div>
  <div class="socials"><span class="dot" style="border-color:var(--blue-light)"></span><span class="dot"></span><span class="dot"></span><span class="dot"></span></div>
</article>

<article class="trainer" style="left:824px">
  <svg class="shape" viewBox="0 0 238 200" preserveAspectRatio="none"><polygon points="0,40 238,0 238,200 0,200" fill="var(--blue-light)"/></svg>
  <div class="photo" role="img" aria-label="Portrait of a crossfit trainer" style="background:linear-gradient(180deg,#7a5240,#1b1b1b)"></div>
  <svg class="notch" viewBox="0 0 298 32" preserveAspectRatio="none"><polygon points="0,30 149,2 298,30 298,32 0,32" fill="#fff" stroke="#d6d6d6"/></svg>
  <div class="card"></div>
  <div class="heading name">- Dana Rowe</div>
  <div class="role">Crossfit training</div>
  <div class="socials"><span class="dot"></span><span class="dot"></span><span class="dot"></span><span class="dot"></span></div>
</article>

<!-- Gallery -->
<section class="gallery" role="img" aria-label="Video still of a woman doing floor exercises on a mat"></section>
<h2 class="heading section-title" style="top:1994px">Gallery</h2>
<svg class="chev" style="left:585px;top:2080px" viewBox="0 0 30 22"><path d="M4 3l11 7 11-7M4 12l11 7 11-7" fill="none" stroke="var(--yellow)" stroke-width="3"/></svg>
<svg class="abs" style="left:568px;top:2268px" width="64" height="64" viewBox="0 0 64 64"><circle cx="32" cy="32" r="29" fill="none" stroke="var(--yellow)" stroke-width="3"/><polygon points="25,19 46,32 25,45" fill="var(--yellow)"/></svg>

<div class="thumbs">
  <div class="thumb" role="img" aria-label="Gallery photo of training on a mat" style="background:linear-gradient(135deg,#3a4048,#1b1b1b)"></div>
  <div class="thumb" role="img" aria-label="Gallery photo of a trainer with a member" style="background:linear-gradient(135deg,#c4423a,#e8e8e8)"></div>
  <div class="thumb" role="img" aria-label="Gallery photo of a group class" style="background:linear-gradient(135deg,#8a8a8a,#d8d8d8)"></div>
  <div class="thumb" role="img" aria-label="Gallery photo of an athlete lifting" style="background:linear-gradient(135deg,#6a6a6a,#2a2a2a)"></div>
  <div class="thumb" role="img" aria-label="Gallery photo of a cycling class" style="background:linear-gradient(135deg,#c6cfd8,#6a7a8a)"></div>
  <div class="thumb" role="img" aria-label="Gallery photo of dumbbell training" style="background:linear-gradient(135deg,#5a6a7a,#c8a070)"></div>
  <div class="thumb" role="img" aria-label="Gallery photo of an outdoor bootcamp" style="background:linear-gradient(135deg,#8fb0d0,#9a8a6a)"></div>
  <div class="thumb" role="img" aria-label="Gallery photo of a gym workout" style="background:linear-gradient(135deg,#4a3a3a,#8a5a4a)"></div>
</div>

<!-- Map & Contact -->
<div class="map" role="img" aria-label="Street map showing the gym location"></div>
<div class="abs" style="left:30px;top:2654px;width:130px;height:36px;background:#fff;box-shadow:0 1px 4px rgba(0,0,0,.2);font-size:13px;color:#999;padding:10px 12px">Visit us from...</div>
<div class="abs" style="left:170px;top:2876px;width:86px;height:62px;background:#fff;display:flex;align-items:center;justify-content:center;gap:6px"><span style="width:18px;height:18px;border-radius:50%;background:var(--blue)"></span><span style="font-family:Oswald,Arial,sans-serif;font-weight:700;font-size:11px;color:var(--yellow);text-transform:uppercase;line-height:1">Coreline<br>Fitness Hub</span></div>

<h2 class="heading section-title" style="left:450px;width:480px;top:2718px;font-size:38px">Contact us</h2>
<div class="field" style="left:447px;top:2795px;width:284px;height:50px">Name *</div>
<div class="field" style="left:738px;top:2795px;width:295px;height:50px">Email Id *</div>
<div class="field" style="left:447px;top:2852px;width:586px;height:154px">Message *</div>
<div class="field" style="left:447px;top:3014px;width:488px;height:50px">File...</div>
<div class="field" style="left:942px;top:3014px;width:91px;height:50px;display:flex;align-items:center;justify-content:center;gap:5px;padding:0"><span style="width:7px;height:7px;border-radius:50%;background:var(--blue)"></span><span style="width:7px;height:7px;border-radius:50%;background:var(--blue)"></span><span style="width:7px;height:7px;border-radius:50%;background:var(--blue)"></span></div>
<div class="btn btn-yellow" style="left:645px;top:3078px;width:180px;height:44px">Submit</div>

<!-- Footer -->
<footer class="footer" role="img" aria-label="Faint photo of an athlete's torso over blue"></footer>
<svg class="chev" style="left:585px;top:3332px" viewBox="0 0 30 22"><path d="M4 3l11 7 11-7M4 12l11 7 11-7" fill="none" stroke="var(--blue)" stroke-width="3"/></svg>
<div class="foot-brand">
  <div style="display:flex;align-items:center;gap:10px"><span style="width:50px;height:50px;border-radius:50%;background:var(--silver)"></span><span style="font-family:Oswald,Arial,sans-serif;font-weight:700;font-size:24px;color:var(--white);text-transform:uppercase;line-height:1">Coreline<br>Fitness Hub</span></div>
  <p class="foot-text" style="white-space:nowrap">Lorem ipsum dolor sit amet, consectetur adipiscing</p>
</div>
<div class="foot-social"><span class="dot on"></span><span class="dot"></span><span class="dot"></span><span class="dot"></span></div>

<div class="foot-info" style="top:3432px">
  <svg width="18" height="18" viewBox="0 0 18 18"><path d="M9 1C5.7 1 3 3.6 3 6.9 3 11.3 9 17 9 17s6-5.7 6-10.1C15 3.6 12.3 1 9 1zm0 8.2a2.3 2.3 0 110-4.6 2.3 2.3 0 010 4.6z" fill="#cfdff0"/></svg>
  <span style="width:520px">Lorem ipsum dolor sit amet, consectetur adipiscing elit, sed do eiusmod tempor incididunt ut.</span>
</div>
<div class="foot-info" style="top:3502px">
  <svg width="18" height="18" viewBox="0 0 18 18"><path d="M4 1l3 4-2 2c1 2 3 4 5 5l2-2 4 3-2 3C8 16 2 10 1 3z" fill="#cfdff0"/></svg>
  <span>+123 456 7890</span>
</div>
<div class="foot-info" style="top:3540px">
  <svg width="18" height="18" viewBox="0 0 18 18"><rect x="1" y="4" width="16" height="11" fill="#cfdff0"/><path d="M1 4l8 6 8-6" fill="none" stroke="#1f6fb9" stroke-width="1.5"/></svg>
  <span>hello@corelinefitnesshub.com</span>
</div>

<div class="copyright">© <b>Coreline Fitness Hub</b> - 2017. All Rights Reserved.</div>

</body>
</html>
```